real esate business card with company logo and name

we need a business card design for a real esate company

The company name is Walsh & Brand Pty Ltd, and we have our logo designed and will upload. We want classic or moden feel. Black or white background. looks more textured. Should include folowinginformations
Owen Walsh and Lucy Brand
Sales Agents & Onsite Manager
p: 07 5948 2063
F: 07 5948 2174
M:0431 857 219
3/42 Marlow Crescent, FERNLEA QLD 4213

We want this business card looks professonal. Thank you in advance.

Industry/Entity Type

Real Estate Agent

Contact Information for Business Card

Owen Walsh and Lucy Brand
Onsite Manager & Sales Agents
p: 07 5948 2063
M:0431 857 219

Font styles to use
Serif

Colors
000000
fbfbfb
333333
959595

Requirements
Must have
• company logo and name, black or white back ground

```html
<!DOCTYPE html>
<html lang="en">
<head>
<meta charset="utf-8">
<title>Walsh &amp; Brand Pty Ltd — Business Card</title>
<link rel="stylesheet" href="https://fonts.googleapis.com/css2?family=Oswald:wght@300;400&family=Noto+Sans:wght@400&display=swap">
<style>
  :root {
    --backdrop: #a3a0a0;
    --card-black: #131518;
    --card-white: #fbfbfb;
    --ink-dark: #333333;
    --ink-mid: #4a4a4a;
    --ink-grey: #959595;
    --mark-grey: #6e6e70;
    --band-dark: #58585a;
    --band-light: #c4c4c6;
  }
  * { margin: 0; padding: 0; box-sizing: border-box; }
  html, body { width: 1200px; height: 1200px; overflow: hidden; }
  body { background: var(--backdrop); position: relative; font-family: "Noto Sans", sans-serif; }

  .card { position: absolute; width: 712px; height: 418px; border-radius: 28px; overflow: hidden; }
  .card--front { left: 238px; top: 118px; background: var(--card-black); }
  .card--back { left: 231px; top: 644px; background: var(--card-white); }

  .brand-square { position: absolute; background: var(--mark-grey); }
  .card--front .brand-square { width: 96px; height: 96px; left: 308px; top: 140px; }
  .card--back .brand-square { width: 110px; height: 110px; left: 114px; top: 130px; }

  .brand-name {
    position: absolute; font-family: "Oswald", sans-serif; font-weight: 300;
    color: var(--ink-grey); letter-spacing: 0.5px; white-space: nowrap;
  }
  .card--front .brand-name { left: 0; width: 712px; text-align: center; top: 288px; font-size: 24px; }
  .card--back .brand-name { left: 20px; width: 298px; text-align: center; top: 278px; font-size: 24px; }

  .person-names {
    position: absolute; left: 381px; top: 86px; font-family: "Oswald", sans-serif;
    font-weight: 400; font-size: 26px; color: var(--ink-mid); white-space: nowrap;
  }
  .person-role {
    position: absolute; left: 381px; top: 128px; font-family: "Oswald", sans-serif;
    font-weight: 400; font-size: 15px; color: var(--ink-mid);
  }
  .contact-list { position: absolute; left: 381px; top: 188px; list-style: none; }
  .contact-list li {
    display: flex; align-items: center; height: 26.5px;
    font-size: 17px; color: var(--ink-mid);
  }
  .contact-list svg { width: 17px; height: 17px; margin-right: 18px; fill: none; stroke: var(--ink-grey); stroke-width: 1.6; }
  .contact-list svg .solid { fill: var(--ink-grey); stroke: none; }
  .address {
    position: absolute; left: 381px; top: 274px; font-size: 17px;
    line-height: 28px; color: var(--ink-mid);
  }
  .card-band { position: absolute; left: 0; bottom: 0; width: 712px; height: 20px; }
</style>
</head>
<body>

  <section class="card card--front" aria-label="Card front">
    <div class="brand-square"></div>
    <p class="brand-name">WALSH &amp; BRAND PTY LTD.</p>
  </section>

  <section class="card card--back" aria-label="Card back">
    <div class="brand-square"></div>
    <p class="brand-name">WALSH &amp; BRAND PTY LTD.</p>

    <h1 class="person-names">Owen Walsh &amp; Lucy Brand</h1>
    <p class="person-role">Sales Agents &amp; Onsite Manager</p>

    <ul class="contact-list">
      <li>
        <svg viewBox="0 0 16 16" aria-hidden="true"><rect x="4" y="1" width="8" height="14" rx="1.5"/><circle class="solid" cx="8" cy="12.5" r="0.9"/></svg>
        0431 857 219
      </li>
      <li>
        <svg viewBox="0 0 16 16" aria-hidden="true"><path class="solid" d="M1 6c0-2 3-3 7-3s7 1 7 3v1.5h-3.5V6h-7v1.5H1z"/><path class="solid" d="M4 8h8l2 6H2z"/></svg>
        07 5948 2063
      </li>
      <li>
        <svg viewBox="0 0 16 16" aria-hidden="true"><rect class="solid" x="4" y="1" width="8" height="4"/><rect class="solid" x="1" y="6" width="14" height="6" rx="1"/><rect class="solid" x="4" y="11" width="8" height="4"/></svg>
        07 5948 2174
      </li>
    </ul>

    <p class="address">3/42 Marlow Crescent,<br>FERNLEA QLD 4213</p>

    <svg class="card-band" viewBox="0 0 712 20" preserveAspectRatio="none" aria-hidden="true">
      <polygon points="0,0 494,0 470,20 0,20" fill="var(--band-dark)"/>
      <polygon points="500,0 712,0 712,20 470,20" fill="var(--band-light)"/>
    </svg>
  </section>

</body>
</html>
```